Boutique town planning business needs a Business Card design

We need a business card design for a new company called The Zoning Bridgeway. We provide town planning and urban design services to government, business and community groups. We would like to see the designs use the colours in the logo (blue, deep red, green and amber), plenty of white and including black and grey in the writing. The final design should communicate collaboration, creativity and professionalism and that we are approachable.

Industry/Entity Type

Town

```html
<!DOCTYPE html>
<html lang="en">
<head>
<meta charset="utf-8">
<title>The Zoning Bridgeway – Business Card</title>
<link href="https://fonts.googleapis.com/css2?family=Open+Sans:wght@400;600;700&display=swap" rel="stylesheet">
<style>
  :root {
    --backdrop: #3a3a3c;
    --card-white: #ffffff;
    --card-grey: #e6e6e6;
    --band-black: #0b0b0b;
    --brand-green: #2f9e2b;
    --ink-dark: #2b2b2b;
    --ink-mid: #3c3c3c;
  }
  html, body {
    margin: 0;
    width: 1200px;
    height: 816px;
    overflow: hidden;
    background: var(--backdrop);
    font-family: "Open Sans", Arial, sans-serif;
  }
  .card {
    position: absolute;
    left: 75px;
    top: 108px;
    width: 1050px;
    height: 600px;
    border-radius: 44px;
    overflow: hidden;
  }
  .card-shapes {
    position: absolute;
    inset: 0;
  }
  .identity {
    position: absolute;
    left: 90px;
    top: 190px;
    color: var(--ink-dark);
  }
  .identity-name {
    margin: 0;
    font-size: 34px;
    font-weight: 700;
    letter-spacing: 0.5px;
  }
  .identity-role {
    margin: 2px 0 0;
    font-size: 24px;
    font-weight: 400;
  }
  .contact-list {
    position: absolute;
    left: 90px;
    top: 315px;
    margin: 0;
    padding: 0;
    list-style: none;
    color: var(--ink-mid);
    font-size: 20px;
    line-height: 30px;
  }
  .contact-item {
    display: flex;
    align-items: flex-start;
    gap: 10px;
  }
  .contact-item svg {
    flex: none;
    width: 18px;
    height: 18px;
    margin-top: 6px;
    fill: var(--ink-dark);
  }
  .contact-address {
    font-weight: 700;
    width: 280px;
    margin-bottom: 4px;
  }
  .brand {
    position: absolute;
    right: 70px;
    top: 70px;
    display: flex;
    flex-direction: column;
    align-items: center;
  }
  .brand-circle {
    width: 120px;
    height: 120px;
    border-radius: 50%;
    background: var(--brand-green);
  }
  .brand-name {
    margin-top: 14px;
    font-size: 30px;
    font-weight: 700;
    line-height: 1.05;
    color: var(--ink-dark);
    text-align: center;
  }
  .website {
    position: absolute;
    left: 600px;
    top: 372px;
    width: 420px;
    height: 76px;
    display: flex;
    align-items: center;
    justify-content: center;
    color: var(--card-white);
    font-size: 30px;
    font-weight: 400;
  }
</style>
</head>
<body>
  <div class="card">
    <svg class="card-shapes" viewBox="0 0 1050 600" width="1050" height="600" aria-hidden="true">
      <defs>
        <linearGradient id="card-face" x1="0" y1="0" x2="1" y2="1">
          <stop offset="0" stop-color="var(--card-white)"/>
          <stop offset="1" stop-color="var(--card-grey)"/>
        </linearGradient>
      </defs>
      <rect width="1050" height="600" fill="var(--band-black)"/>
      <path d="M0 0 H1050 V372 H600 C570 372 560 392 555 420 C550 455 540 470 500 470 H0 Z" fill="url(#card-face)"/>
      <path d="M1050 372 V450 H620 C580 450 562 430 562 411 C562 390 580 372 620 372 Z" fill="var(--brand-green)"/>
    </svg>

    <div class="identity">
      <h1 class="identity-name">DANIEL WHITMORE</h1>
      <p class="identity-role">Managing Director</p>
    </div>

    <ul class="contact-list">
      <li class="contact-item contact-address">
        <svg viewBox="0 0 24 24"><path d="M12 2a7 7 0 0 0-7 7c0 5.2 7 13 7 13s7-7.8 7-13a7 7 0 0 0-7-7zm0 9.5A2.5 2.5 0 1 1 12 6.5a2.5 2.5 0 0 1 0 5z"/></svg>
        <span>12 Harbour Lane, Level 4, Eastfield</span>
      </li>
      <li class="contact-item">
        <svg viewBox="0 0 24 24"><path d="M6.6 10.8a15.1 15.1 0 0 0 6.6 6.6l2.2-2.2a1 1 0 0 1 1-.25 11.4 11.4 0 0 0 3.6.6 1 1 0 0 1 1 1V20a1 1 0 0 1-1 1A17 17 0 0 1 3 4a1 1 0 0 1 1-1h3.5a1 1 0 0 1 1 1c0 1.25.2 2.45.6 3.6a1 1 0 0 1-.25 1z"/></svg>
        <span>021 555 0148</span>
      </li>
      <li class="contact-item">
        <svg viewBox="0 0 24 24"><path d="M7 2h10a2 2 0 0 1 2 2v16a2 2 0 0 1-2 2H7a2 2 0 0 1-2-2V4a2 2 0 0 1 2-2zm0 3v12h10V5zm5 13.5a1.2 1.2 0 1 0 0 2.4 1.2 1.2 0 0 0 0-2.4z"/></svg>
        <span>021 555 0192</span>
      </li>
      <li class="contact-item">
        <svg viewBox="0 0 24 24"><path d="M2 5h20v14H2zm2 2v.5l8 5 8-5V7zm0 2.9V17h16V9.9l-8 5z"/></svg>
        <span>hello@zoningbridgeway.com</span>
      </li>
    </ul>

    <div class="brand">
      <div class="brand-circle"></div>
      <div class="brand-name">The<br>Zoning Bridgeway</div>
    </div>

    <div class="website">www.zoningbridgeway.com</div>
  </div>
</body>
</html>
```